Mandala Postcard Design

I am in need of a postcard to hand out at a Psychic Fair. I envision the card to having half-of-a Mandala (from my Facebook folder), touched up a bit to make it vibrant and bold. Others vendors will have cards w/photographic backgrounds doing yoga. I'd like mine to stand out for it's line-drawn "cartoonish" nature, solid-color nature. The wording would be my basic contact info and a short description ... something like: "Experience the Magic of Mandala Making ... Next Class will be held: (open space for writing, no lines) The art is contained in this Facebook folder. Lots to choose from, with my favorites being the stronger outlined designs.

https://www.examplesocial.net/Brightorbs/media_set?set=a.20462926615637197.2184852941.783542196&type=3
Updates

I just uploaded a few new drawings that might work better, since they are more round. I want to minimize the white space, for instance, avoid having the left & right corners empty. Another idea could be to use 1/4 mandalas in the corners. I'm ready to make a decision. I want it to look great, but as I gain drawing experience, I'll need to update my cards. Thanks! I'm not sure if this the place for this comment, but I'll also be needing a DVD label for my tutorials, and a front page design for a mandala coloring book.

Target Market(s)

Primarily women interested in metaphysical, psychic, meditation, reiki and a basic interest in art.

Font styles to use
Serif
Sans Serif

Requirements
Should not have
• Should not be on a dark card, really should be a plain white background, it seems, in order to stand out.

```html
<!DOCTYPE html>
<html lang="en">
<head>
<meta charset="utf-8">
<title>Mandala Making Class Postcard</title>
<link rel="stylesheet" href="https://fonts.googleapis.com/css2?family=Sue+Ellen+Francisco&family=Arimo&display=swap">
<style>
  :root {
    --paper: #ffffff;
    --ink: #1a1a1a;
    --coral: #f08a7e;
    --sun: #fbef8a;
    --sky: #4fa6dc;
    --aqua: #5cc8e0;
    --lime: #c6df5a;
    --rose: #e9417c;
    --violet: #7b3f8c;
    --red: #d9262b;
  }
  html, body {
    margin: 0;
    padding: 0;
    overflow: hidden;
    background: var(--paper);
  }
  .postcard {
    position: relative;
    width: 1200px;
    height: 929px;
    overflow: hidden;
    background: var(--paper);
  }
  .mandala {
    position: absolute;
    display: block;
  }
  .mandala--half {
    left: -345px;
    top: 0;
    width: 910px;
    height: 910px;
  }
  .mandala--corner {
    left: 935px;
    top: -45px;
    width: 290px;
    height: 290px;
  }
  .mandala--bloom {
    left: 735px;
    top: 560px;
    width: 500px;
    height: 500px;
  }
  .headline {
    position: absolute;
    left: 560px;
    top: 300px;
    width: 520px;
    margin: 0;
    text-align: center;
    font-family: "Sue Ellen Francisco", cursive;
    font-weight: 400;
    font-size: 56px;
    line-height: 62px;
    color: var(--ink);
  }
  .class-date {
    position: absolute;
    left: 632px;
    top: 470px;
    margin: 0;
    font-family: "Arimo", Arial, sans-serif;
    font-size: 21px;
    color: var(--ink);
  }
</style>
</head>
<body>
<main class="postcard">
  <svg class="mandala mandala--half" viewBox="0 0 910 910" role="img" aria-label="Hand-drawn mandala in coral, yellow, blue and lime with stars, hands and a spiky turquoise border, cut in half by the left edge">
    <defs>
      <radialGradient id="half-tones" cx="50%" cy="50%" r="50%">
        <stop offset="0" stop-color="var(--coral)"/>
        <stop offset="0.28" stop-color="var(--lime)"/>
        <stop offset="0.55" stop-color="var(--sun)"/>
        <stop offset="0.75" stop-color="var(--sky)"/>
        <stop offset="0.88" stop-color="var(--coral)"/>
        <stop offset="1" stop-color="var(--aqua)"/>
      </radialGradient>
    </defs>
    <circle cx="455" cy="455" r="455" fill="url(#half-tones)"/>
  </svg>

  <svg class="mandala mandala--corner" viewBox="0 0 290 290" role="img" aria-label="Small hand-drawn mandala in pink, yellow and blue with red petal accents, cut by the top edge">
    <defs>
      <radialGradient id="corner-tones" cx="50%" cy="50%" r="50%">
        <stop offset="0" stop-color="var(--sun)"/>
        <stop offset="0.4" stop-color="var(--rose)"/>
        <stop offset="0.7" stop-color="var(--aqua)"/>
        <stop offset="1" stop-color="#f7b8c8"/>
      </radialGradient>
    </defs>
    <circle cx="145" cy="145" r="140" fill="url(#corner-tones)"/>
  </svg>

  <svg class="mandala mandala--bloom" viewBox="0 0 500 500" role="img" aria-label="Hand-drawn mandala flower with pointed petals in blue, pink, yellow and red, cut by the bottom edge">
    <defs>
      <radialGradient id="bloom-tones" cx="50%" cy="50%" r="50%">
        <stop offset="0" stop-color="var(--violet)"/>
        <stop offset="0.3" stop-color="var(--rose)"/>
        <stop offset="0.6" stop-color="var(--sun)"/>
        <stop offset="0.85" stop-color="var(--sky)"/>
        <stop offset="1" stop-color="#f3a9c4"/>
      </radialGradient>
    </defs>
    <circle cx="250" cy="250" r="245" fill="url(#bloom-tones)"/>
  </svg>

  <h1 class="headline">Experience the Magic of<br>Mandala Making</h1>
  <p class="class-date">Next Class will be held :</p>
</main>
</body>
</html>
```